Home Security Company Business Card

Looking for a eye catching business card that is non traditional and stands out but yet still looks professional. It should include all the pertinent information such as name, title, address, telephone, e-mail, website address should definitely stand out and then finally the logo.

Target Market(s)

Residential and Commercial accounts mostly upscale accounts

Industry/Entity Type

Security

Contact Information for Business Card

Name
Title
Address
Office #
Cell #
E-mail
Website

Font styles to use
Serif
Sans Serif

Requirements
Must have
• Logo, two sided color configuration
Nice to have
• You decide
Should not have
• There really aren't any.

```html
<!DOCTYPE html>
<html lang="en">
<head>
<meta charset="utf-8">
<title>Bastion Home Security Inc. – Business Card</title>
<link rel="stylesheet" href="https://fonts.googleapis.com/css2?family=Cinzel:wght@600&family=Open+Sans:wght@400;600;700&display=swap">
<style>
  :root {
    --maroon: #7a1420;
    --maroon-deep: #5c0d16;
    --maroon-light: #9b2733;
    --gold: #d9a441;
    --gold-text: #c08a25;
    --gold-soft: #f2dcaa;
    --gold-pale: #f8ead0;
    --ink: #3a1a1d;
    --paper: #ffffff;
    --backdrop: #ece7e1;
  }
  * { margin: 0; padding: 0; box-sizing: border-box; }
  html, body { width: 1200px; height: 913px; overflow: hidden; }
  body {
    background: var(--backdrop);
    font-family: "Open Sans", Arial, sans-serif;
    position: relative;
  }
  .card {
    position: absolute;
    width: 540px;
    height: 310px;
    border-radius: 16px;
    overflow: hidden;
    box-shadow: 0 10px 28px rgba(60, 30, 20, 0.22);
  }
  .card--front { left: 40px; top: 301px; background: var(--paper); }
  .card--back {
    left: 620px; top: 301px;
    background: linear-gradient(160deg, var(--maroon-light) 0%, var(--maroon) 45%, var(--maroon-deep) 100%);
  }
  .card__bands { position: absolute; inset: 0; }

  .brand {
    position: absolute;
    display: flex;
    align-items: center;
    gap: 10px;
    font-family: "Cinzel", Georgia, serif;
    font-weight: 600;
    line-height: 1.05;
    letter-spacing: 0.5px;
  }
  .brand__mark { width: 14px; height: 14px; border-radius: 50%; flex: none; }
  .card--front .brand { right: 34px; top: 40px; color: var(--maroon); font-size: 18px; }
  .card--front .brand__mark { background: var(--gold); }
  .card--back .brand { left: 150px; top: 100px; color: var(--paper); font-size: 24px; }
  .card--back .brand__mark { background: var(--gold); width: 18px; height: 18px; }

  .rule { position: absolute; height: 1px; background: var(--maroon); opacity: 0.7; }
  .rule--main { left: 34px; right: 34px; top: 132px; }

  .holder { position: absolute; left: 34px; top: 96px; }
  .holder__name { font-size: 24px; font-weight: 700; color: var(--maroon); line-height: 1.2; }
  .holder__title { margin-top: 8px; font-size: 14px; font-weight: 600; color: var(--gold-text); }

  .contact {
    position: absolute;
    right: 34px;
    text-align: right;
    font-size: 13.5px;
    color: var(--ink);
    line-height: 1.4;
  }
  .contact--address { top: 144px; right: 53px; }
  .contact--lines { top: 192px; }
  .contact__line { display: flex; justify-content: flex-end; align-items: center; gap: 8px; }
  .contact__icon { width: 11px; height: 11px; flex: none; }

  .site-band {
    position: absolute;
    left: 0; right: 0; top: 222px;
    height: 36px;
    background: var(--paper);
    display: flex;
    align-items: center;
    justify-content: space-between;
    padding: 0 20px;
  }
  .site-band__url { font-size: 16px; font-weight: 600; color: var(--maroon); }
  .site-band__arrows { width: 62px; height: 16px; }
</style>
</head>
<body>

<section class="card card--front" aria-label="Business card front">
  <svg class="card__bands" viewBox="0 0 540 310" aria-hidden="true">
    <polygon points="0,200 90,200 230,310 0,310" fill="var(--gold-soft)" opacity="0.75"/>
    <polygon points="70,262 140,262 180,310 100,310" fill="var(--paper)"/>
    <polygon points="0,262 50,262 100,310 0,310" fill="var(--gold-pale)"/>
    <polygon points="0,262 40,262 70,310 20,310" fill="var(--maroon)" opacity="0.55"/>
  </svg>

  <div class="brand"><span class="brand__mark"></span><span>Bastion<br>Home Security Inc.</span></div>

  <div class="rule rule--main"></div>

  <div class="holder">
    <div class="holder__name">Daniel Marlowe</div>
    <div class="holder__title">Owner</div>
  </div>

  <div class="contact contact--address">
    <div>742 Harbor Lane</div>
    <div>Aurora, Illinois 60505</div>
  </div>

  <div class="contact contact--lines">
    <div class="contact__line">+330 2460-5512
      <svg class="contact__icon" viewBox="0 0 12 12" aria-hidden="true"><rect x="1" y="4" width="10" height="7" rx="1.5" fill="none" stroke="var(--gold)" stroke-width="1.3"/><path d="M2 4 Q6 0 10 4" fill="none" stroke="var(--gold)" stroke-width="1.3"/></svg>
    </div>
    <div class="contact__line">+330 2540-4418
      <svg class="contact__icon" viewBox="0 0 12 12" aria-hidden="true"><path d="M2 1 L4.5 1 L5.5 4 L4 5 Q5 8 7 8.5 L8 7 L11 8 L11 10.5 Q6 12 2 6 Q1 3 2 1Z" fill="var(--gold)"/></svg>
    </div>
    <div class="contact__line">info@danielmarlowemail.com
      <svg class="contact__icon" viewBox="0 0 12 12" aria-hidden="true"><rect x="0.7" y="2.5" width="10.6" height="7" fill="none" stroke="var(--gold)" stroke-width="1.2"/><path d="M0.7 2.5 L6 7 L11.3 2.5" fill="none" stroke="var(--gold)" stroke-width="1.2"/></svg>
    </div>
  </div>
</section>

<section class="card card--back" aria-label="Business card back">
  <div class="brand"><span class="brand__mark"></span><span>Bastion<br>Home Security Inc.</span></div>

  <div class="site-band">
    <svg class="site-band__arrows" viewBox="0 0 62 16" aria-hidden="true">
      <polygon points="0,0 14,8 0,16" fill="var(--maroon)"/>
      <polygon points="22,0 36,8 22,16" fill="var(--maroon)"/>
      <polygon points="44,0 58,8 44,16" fill="var(--maroon)"/>
    </svg>
    <span class="site-band__url">www.bastionhomesecurityinc.com</span>
    <svg class="site-band__arrows" viewBox="0 0 62 16" aria-hidden="true">
      <polygon points="18,0 4,8 18,16" fill="var(--maroon)"/>
      <polygon points="40,0 26,8 40,16" fill="var(--maroon)"/>
      <polygon points="62,0 48,8 62,16" fill="var(--maroon)"/>
    </svg>
  </div>
</section>

</body>
</html>
```